I need a business card designed using the logo provided either vertical or horizontal......Harbourline Property Group is an Australian based real estate company that caters for the upper end of the market so the design of the business card "must reflect" the companies image!!
Colour combinations are optional but "must be realistic" and must be able to be accurately useable CMYK colours.
Please consider that any colours used "must be able to be used" and be suitable in following designs for "pull out banner signs" and "real estate signs".
The colours and the font in the attached designs are for example and other combinations are encouraged.
Target Market(s)
The High End of the Australian real estate market
Industry/Entity Type
Business
Contact Information for Business Card
Logo - Business Name - Director + Licensed Real Estate Agent - Mobile Number (Cell Phone) - Business Number - Fax - Email Address - Web address
Requirements
Must have
- Designs and colours (CMYK) that can easily be interpreted by an Australian printer.
Nice to have
- Some alternative ideas on colour and font..........the ones provided are ok and have been provided as an example but I am looking for alternative ideas
Should not have
- Loud, overly bright colours. Designs that do not reflect the professional standards of the business.
- Designs that look good on a computer monitor but can not be re-created on a printing press.............this is most important when it comes to shading etc.

```html
<!DOCTYPE html>
<html lang="en">
<head>
<meta charset="utf-8">
<title>Harbourline Property Group – Business Card</title>
<link rel="stylesheet" href="https://fonts.googleapis.com/css2?family=Lato:wght@400;700;900&display=swap">
<style>
  :root {
    --backdrop: #2a2a2a;
    --card: #ffffff;
    --card-shade: #ececec;
    --gold: #a87a2c;
    --ink: #2b2b2b;
    --on-gold: #ffffff;
  }
  html, body {
    margin: 0;
    padding: 0;
    width: 1200px;
    height: 873px;
    overflow: hidden;
    background: var(--backdrop);
    font-family: "Lato", Arial, sans-serif;
  }
  .canvas {
    position: relative;
    width: 1200px;
    height: 873px;
  }
  .card {
    position: absolute;
    width: 540px;
    height: 310px;
    border-radius: 22px;
    background: linear-gradient(180deg, var(--card) 0%, var(--card) 70%, var(--card-shade) 100%);
    overflow: hidden;
  }
  .card--back { left: 40px; top: 110px; }
  .card--front { left: 620px; top: 450px; }

  /* Company name */
  .brand-block {
    position: absolute;
    inset: 0;
    display: flex;
    align-items: center;
    justify-content: center;
    gap: 14px;
  }
  .brand-mark {
    flex: none;
    width: 34px;
    height: 34px;
    background: var(--gold);
  }
  .brand-name {
    font-weight: 900;
    font-size: 30px;
    line-height: 1.05;
    letter-spacing: 1px;
    text-transform: uppercase;
    color: var(--ink);
  }
  .front-brand {
    position: absolute;
    left: 30px;
    top: 34px;
    display: flex;
    align-items: center;
    gap: 12px;
  }
  .front-brand .brand-mark { width: 26px; height: 26px; }
  .front-brand .brand-name { font-size: 22px; }

  /* Gold band */
  .gold-band {
    position: absolute;
    left: 0;
    top: 0;
    width: 540px;
    height: 310px;
  }
  .band-fill, .band-emblem { fill: var(--gold); }

  /* Person */
  .person {
    position: absolute;
    left: 28px;
    top: 160px;
    display: inline-flex;
    flex-direction: column;
    align-items: flex-end;
  }
  .person-name {
    margin: 0;
    font-weight: 700;
    font-size: 24px;
    line-height: 1.1;
    color: var(--on-gold);
  }
  .person-role {
    margin: 2px 0 0;
    font-weight: 700;
    font-size: 15px;
    line-height: 1.1;
    color: var(--ink);
  }

  /* Contact */
  .contact-web {
    position: absolute;
    left: 168px;
    top: 224px;
    font-size: 14px;
    line-height: 1;
    color: var(--on-gold);
  }
  .contact-list {
    position: absolute;
    left: 28px;
    top: 246px;
    margin: 0;
    padding: 0;
    list-style: none;
    font-size: 14px;
    line-height: 1;
    color: var(--on-gold);
  }
  .contact-list li {
    display: flex;
    align-items: center;
    gap: 10px;
    margin-bottom: 10px;
  }
  .contact-icon { width: 13px; height: 13px; fill: var(--on-gold); }
  .address {
    position: absolute;
    right: 26px;
    bottom: 20px;
    font-weight: 700;
    font-size: 14px;
    letter-spacing: 1px;
    color: var(--ink);
  }
</style>
</head>
<body>
<main class="canvas">

  <section class="card card--back" aria-label="Card back">
    <div class="brand-block">
      <span class="brand-mark"></span>
      <span class="brand-name">Harbourline<br>Property Group</span>
    </div>
  </section>

  <section class="card card--front" aria-label="Card front">
    <svg class="gold-band" viewBox="0 0 540 310" aria-hidden="true">
      <path class="band-fill" d="M0 150 L400 105 C368 140 376 182 440 205 L290 310 L0 310 Z"/>
      <circle class="band-emblem" cx="475" cy="140" r="30"/>
    </svg>

    <div class="front-brand">
      <span class="brand-mark"></span>
      <span class="brand-name">Harbourline<br>Property Group</span>
    </div>

    <div class="person">
      <p class="person-name">Clara Whitcombe</p>
      <p class="person-role">President</p>
    </div>

    <span class="contact-web">harbourlineproperty.com</span>

    <ul class="contact-list">
      <li>
        <svg class="contact-icon" viewBox="0 0 16 16" aria-hidden="true"><path d="M3 1h3l1.5 4-2 1.3a9 9 0 0 0 4.2 4.2L11 8.5l4 1.5v3a2 2 0 0 1-2 2A12 12 0 0 1 1 3a2 2 0 0 1 2-2z"/></svg>
        0400318627
      </li>
      <li>
        <svg class="contact-icon" viewBox="0 0 16 16" aria-hidden="true"><path d="M1 3h14v10H1z"/><path d="M1 3l7 6 7-6" fill="none" stroke="#a87a2c" stroke-width="1.4"/></svg>
        clara@harbourlineproperty.com
      </li>
    </ul>

    <span class="address">PO Box 218, Tallai</span>
  </section>

</main>
</body>
</html>
```